Business Card Design

Business Card for professional consulting firm working with large financial institutions.

Target Market(s)

Executive buyers

Industry/Entity Type

Banking

Contact Information for Business Card

Mild creativity wanted. Not boring, but do elaborate artwork.

Font styles to use
Serif
Sans Serif

Colors

Designer to choose colors to be used in the design.

Requirements
Must have
• Standard business card features - company name, individual name, telephone, website, email, locations.
Nice to have
• Two colors
Should not have
• too many colors, fancy printing, cartoons.

```html
<!DOCTYPE html>
<html lang="en">
<head>
<meta charset="utf-8">
<title>Alderpoint Business Card</title>
<link rel="stylesheet" href="https://fonts.googleapis.com/css2?family=Roboto+Slab:wght@300&family=Roboto:wght@400;500&display=swap">
<style>
  :root {
    --backdrop: #dedede;
    --card-white: #f7f7f7;
    --ink: #000000;
    --swoosh: #b5b5b5;
    --back-grey: #a8a8a8;
    --text-light: #ffffff;
    --text-dark: #111111;
  }
  * { margin: 0; padding: 0; box-sizing: border-box; }
  html, body { width: 1200px; height: 960px; overflow: hidden; }
  body { background: var(--backdrop); position: relative; font-family: "Roboto", Arial, sans-serif; }

  .card { position: absolute; width: 600px; height: 342px; overflow: hidden; }
  .card--front { left: 314px; top: 113px; background: var(--card-white); }
  .card--back { left: 311px; top: 472px; background: var(--back-grey); }

  .front-shapes { position: absolute; inset: 0; }

  .brand-name {
    position: absolute; left: 0; right: 0; top: 72px; text-align: center;
    font-family: "Roboto", Arial, sans-serif; font-weight: 400; font-size: 30px;
    line-height: 36px; color: var(--text-dark);
  }

  .holder { position: absolute; right: 326px; top: 248px; text-align: right; color: var(--text-light); }
  .holder__name { font-family: "Roboto Slab", Georgia, serif; font-weight: 300; font-size: 22px; line-height: 1.1; }
  .holder__title { font-weight: 500; font-size: 14px; margin-top: 4px; letter-spacing: 0.3px; }

  .divider { position: absolute; left: 300px; top: 226px; width: 1px; height: 94px; background: var(--text-light); }

  .contact { position: absolute; left: 326px; top: 228px; color: var(--text-light); font-size: 14px; line-height: 18px; }
  .contact__address { margin-bottom: 11px; }
  .contact__line { display: flex; align-items: center; gap: 7px; margin-bottom: 2px; }
  .contact__icon { width: 14px; height: 12px; fill: var(--text-light); }

  .back-name {
    position: absolute; left: 0; right: 0; top: 116px; text-align: center;
    font-family: "Roboto", Arial, sans-serif; font-weight: 400; font-size: 56px;
    line-height: 64px; color: var(--ink);
  }
  .back-url {
    position: absolute; left: 0; right: 0; top: 281px; text-align: center;
    font-size: 14px; letter-spacing: 5px; color: var(--text-dark);
  }
</style>
</head>
<body>
  <section class="card card--front">
    <svg class="front-shapes" width="600" height="342" viewBox="0 0 600 342">
      <path d="M0,155 Q300,225 600,140 L600,155 Q300,215 0,170 Z" fill="var(--swoosh)"/>
      <path d="M0,170 Q300,228 600,172 L600,342 L0,342 Z" fill="var(--ink)"/>
    </svg>
    <div class="brand-name">alderpoint</div>
    <div class="holder">
      <div class="holder__name">DANIEL MARSH</div>
      <div class="holder__title">CEO/FOUNDER</div>
    </div>
    <div class="divider"></div>
    <div class="contact">
      <div class="contact__address">214 Birchwood Court<br>Juneau, Alaska 99801</div>
      <div class="contact__line">
        <svg class="contact__icon" viewBox="0 0 24 24"><path d="M6.6 10.8a15.1 15.1 0 0 0 6.6 6.6l2.2-2.2a1 1 0 0 1 1-.25 11.4 11.4 0 0 0 3.6.57 1 1 0 0 1 1 1V20a1 1 0 0 1-1 1A17 17 0 0 1 3 4a1 1 0 0 1 1-1h3.5a1 1 0 0 1 1 1c0 1.250.2 2.450.57 3.57a1 1 0 0 1-.25 1z"/></svg>
        <span>555 210 4837</span>
      </div>
      <div class="contact__line">
        <svg class="contact__icon" viewBox="0 0 24 18"><path d="M0 0h24v2L12 10 0 2z M0 4.5l12 8 12-8V18H0z"/></svg>
        <span>info@alderpoint.com</span>
      </div>
    </div>
  </section>

  <section class="card card--back">
    <div class="back-name">alderpoint</div>
    <div class="back-url">www.alderpoint.com</div>
  </section>
</body>
</html>
```